Hardcore nerd needs to stand out in a sea of dull Defence business cards

Wombarra Devices is a new Australian consulting engineering company that turns research and theory into practical systems. No evangelistic fluff, just mathematics and physics into electronic and optical circuits for consumer products, scientific research or Defence applications.

We already have a recognised logo (provided) which is often dark blue/black on a light background but we're open to other combinations. (Us engineers tend to have limited aesthetic imagination :)

Some of our recent products have included:
* Instrumentation for electrical testing,
* Radar jammers,
* GPS antenna design,
* Satellite tracking systems,
* High power lasers

We're open to both single and double-sided designs - happy to be convinced either way.

P.S. Another group is working on the web page, so - alas - our web site is currently of no use for images/ideas...

Target Market(s)

Engineering managers,
Scientists

Contact Information for Business Card

Dr Colin Harte
R&D Engineer

colin@wombarradevices.com.au
0427 563 710

PO Box XXX (to be confirmed)
Kelsby ACT 2917
Australia

Font styles to use
Serif
Sans Serif

Colors

Designer to choose colors to be used in the design.

Requirements
Must have
• My contact details!
• I've had many (great) "bold and plain" designs submitted already, so feel free to be artistically creative :)
• Happy to take advice re fonts/colours/printability etc.
Nice to have
• I'm not sure if "lists" are more at home on a CV than a business card, but representative services include:
• Applied electromagnetics
• RF and high speed electronics
• Signal and image processing
• Electro-optical and laser systems
• Concept-to-prototype design services
• If you're considering double sided cards, then often measuring/alignment grids/rulers feature on the back of similar cards.
• e.g. https://www.veltranoptics.example/newgrouppage9.cfm?objectgroup_id=4183
• https://www.veltranoptics.example/newgrouppage9.cfm?objectgroup_ID=4185
• ..or even a "Smith chart" (google will return lots)
• Generic images to represent a capability might work - googling images associated with keyword for each of these areas might help:
• - "passive radar", "phased array", "fdtd", "vircator"
• RF and high speed electronic design
• - "smith chart", "microstrip circuits", "dimensioned drawing", "electronic schematic"
• - "dft", "iir filter"
• - "optical cavity". "laser energy level diagram"
• Background/watermarked images outlines/wireframes/schematics would probably look OK.
Should not have
• If a list of projects/services is provided, it is important not to make the client feel that this is "all" the company can do. Engineering design is a creative discipline (like graphics :)
• Please, no stock "military" snaps like planes, missiles, etc!

```html
<!DOCTYPE html>
<html lang="en">
<head>
<meta charset="utf-8">
<title>Wombarra Devices – Business Card</title>
<link rel="stylesheet" href="https://fonts.googleapis.com/css2?family=Lato:wght@400;700&family=Arimo:wght@700&display=swap">
<style>
  :root {
    --backdrop: #8c8c8c;
    --card-navy: #001f5c;
    --ink-white: #ffffff;
    --rule-blue: #6f86b8;
  }
  * { margin: 0; padding: 0; box-sizing: border-box; }
  html, body {
    width: 1200px;
    height: 900px;
    overflow: hidden;
    background: var(--backdrop);
  }
  .canvas {
    position: relative;
    width: 1200px;
    height: 900px;
  }
  .card {
    position: absolute;
    top: 258px;
    width: 398px;
    height: 397px;
    border-radius: 28px;
    background: var(--card-navy);
    color: var(--ink-white);
  }
  .card--front { left: 197px; }
  .card--back { left: 623px; }

  /* Front: brand lockup */
  .brand {
    position: absolute;
    left: 46px;
    top: 147px;
    display: flex;
    align-items: center;
    gap: 22px;
  }
  .brand__dot {
    width: 82px;
    height: 82px;
    border-radius: 50%;
    background: var(--ink-white);
    flex: none;
  }
  .brand__name {
    font-family: "Lato", sans-serif;
    font-weight: 700;
    font-size: 31px;
    line-height: 1.05;
    letter-spacing: 0.5px;
    text-transform: uppercase;
  }

  /* Back: contact details */
  .contact {
    position: absolute;
    inset: 0;
    text-align: center;
    font-family: "Lato", sans-serif;
    font-size: 19px;
  }
  .contact__name {
    position: absolute;
    left: 0; right: 0;
    top: 74px;
    font-family: "Arimo", sans-serif;
    font-weight: 700;
    font-size: 24px;
    letter-spacing: 0.3px;
  }
  .contact__role {
    position: absolute;
    left: 0; right: 0;
    top: 101px;
  }
  .contact__icons {
    position: absolute;
    left: 88px;
    top: 138px;
    width: 208px;
    height: 28px;
  }
  .contact__lines {
    position: absolute;
    left: 0; right: 0;
    top: 171px;
    line-height: 24px;
  }
  .contact__rule {
    position: absolute;
    left: 89px;
    top: 259px;
    width: 213px;
    height: 1px;
    background: var(--rule-blue);
  }
  .contact__address {
    position: absolute;
    left: 0; right: 0;
    top: 270px;
    line-height: 24px;
  }
</style>
</head>
<body>
<main class="canvas">

  <section class="card card--front" aria-label="Card front">
    <div class="brand">
      <span class="brand__dot" aria-hidden="true"></span>
      <p class="brand__name">Wombarra<br>Devices</p>
    </div>
  </section>

  <section class="card card--back" aria-label="Card back">
    <div class="contact">
      <h1 class="contact__name">DR COLIN HARTE</h1>
      <p class="contact__role">R&amp;D Engineer</p>

      <svg class="contact__icons" viewBox="0 0 208 28" aria-hidden="true">
        <line x1="0" y1="14" x2="58" y2="14" stroke="var(--rule-blue)" stroke-width="1"/>
        <line x1="148" y1="14" x2="208" y2="14" stroke="var(--rule-blue)" stroke-width="1"/>
        <!-- phone -->
        <circle cx="73" cy="14" r="13" fill="var(--ink-white)"/>
        <path d="M66 12 q7 -6 14 0 l-2 3 h-3 v-2 h-4 v2 h-3 z" fill="var(--card-navy)"/>
        <rect x="67" y="15" width="12" height="5" rx="1" fill="var(--card-navy)"/>
        <!-- envelope -->
        <circle cx="103" cy="14" r="13" fill="var(--ink-white)"/>
        <rect x="95" y="8.5" width="16" height="11" fill="none" stroke="var(--card-navy)" stroke-width="1.6"/>
        <path d="M95 8.5 l8 6 l8 -6" fill="none" stroke="var(--card-navy)" stroke-width="1.6"/>
        <!-- globe -->
        <circle cx="133" cy="14" r="13" fill="var(--ink-white)"/>
        <circle cx="133" cy="14" r="7.5" fill="none" stroke="var(--card-navy)" stroke-width="1.6"/>
        <ellipse cx="133" cy="14" rx="3.2" ry="7.5" fill="none" stroke="var(--card-navy)" stroke-width="1.3"/>
        <line x1="125.5" y1="14" x2="140.5" y2="14" stroke="var(--card-navy)" stroke-width="1.3"/>
      </svg>

      <p class="contact__lines">
        0427 563 710<br>
        colin@wombarradevices.com.au<br>
        www.wombarradevices.com.au
      </p>

      <div class="contact__rule"></div>

      <p class="contact__address">
        PO Box XXX<br>
        Kelsby ACT 2917, Australia
      </p>
    </div>
  </section>

</main>
</body>
</html>
```